W. Darrow Billboard

2 miles ahead on right
Voted number 1 ... again!
California cuisine
Located in Historic Marbury Hill Inn
Picture of a couple dining
www.torvellis.com 555.317.2968

Target Market(s)

travelers

Industry/Entity Type

hospitality

Font styles to use
Serif

Colors
59FF00
82FF00
B8FF75
E3FFCB
F4FFEA
EE7325
F08F49
F5BC92
FAE3D3
FDF4ED

Requirements
Should not have
• bright colors

```html
<!DOCTYPE html>
<html lang="en">
<head>
<meta charset="utf-8">
<title>Torvelli's Billboard</title>
<link rel="stylesheet" href="https://fonts.googleapis.com/css2?family=Alfa+Slab+One&family=Roboto+Condensed:wght@700&family=Open+Sans:wght@700&display=swap">
<style>
:root{
  --backdrop:#1c1d22;
  --lime-deep:#9fd42a;
  --lime:#c6ec3c;
  --hand:#bfe85a;
  --sheet:#ffffff;
  --red:#d7141a;
  --orange:#ee5a1f;
  --grey:#8b8b8b;
  --green-type:#9ccc1e;
  --photo-warm:#8a6a4a;
  --photo-dark:#3a2d26;
  --gold:#ffd400;
}
*{margin:0;padding:0;box-sizing:border-box}
html,body{width:1200px;height:801px;overflow:hidden;background:var(--backdrop)}
.billboard{
  position:absolute;left:20px;top:75px;width:1160px;height:650px;
  background:linear-gradient(120deg,var(--lime-deep),var(--lime) 55%,var(--lime-deep));
  overflow:hidden;
}
.sheet{
  position:absolute;left:40px;top:40px;width:1080px;height:570px;
  background:var(--sheet);border-radius:18px;
  box-shadow:0 6px 14px rgba(0,0,0,.25);
}
.hand{position:absolute;background:var(--hand)}
.hand--left{left:0;top:70px;width:300px;height:120px;border-radius:0 60px 60px 0}
.hand--right{left:1040px;top:430px;width:120px;height:160px;border-radius:60px 0 0 60px}
.tilt{position:absolute;white-space:nowrap;transform:rotate(6deg);transform-origin:left center}
.arrow{position:absolute;left:290px;top:100px;width:440px;height:80px;transform:rotate(6deg);transform-origin:left center}
.arrow-text{left:320px;top:118px;font:700 26px/1 "Open Sans",sans-serif;color:#fff;letter-spacing:.5px}
.brand{left:760px;top:100px;color:var(--orange);font-family:"Alfa Slab One",serif;text-align:center}
.brand-name{font-size:52px;line-height:1}
.brand-sub{font-size:15px;letter-spacing:2px;margin-top:6px}
.tagline{left:330px;top:198px;font:30px/1 "Alfa Slab One",serif;color:var(--green-type)}
.headline{font:86px/1 "Alfa Slab One",serif;color:var(--green-type);text-shadow:2px 3px 0 rgba(0,0,0,.12)}
.headline--first{left:160px;top:245px}
.headline--second{left:720px;top:300px;font-size:80px}
.venue{left:260px;top:355px;font:700 38px/1 "Roboto Condensed",sans-serif;color:var(--grey);letter-spacing:4px}
.phone{left:330px;top:425px;font:700 62px/1 "Roboto Condensed",sans-serif;color:var(--red);letter-spacing:5px}
.web{left:290px;top:500px;font:700 48px/1 "Roboto Condensed",sans-serif;color:var(--red);letter-spacing:4px}
.badge{position:absolute;left:60px;top:360px;width:180px;height:180px}
.photo{position:absolute;border:5px solid #fff;box-shadow:0 3px 8px rgba(0,0,0,.3)}
.photo--top{left:770px;top:430px;width:150px;height:105px;transform:rotate(4deg);
  background:linear-gradient(135deg,var(--photo-warm),#c9a070)}
.photo--bottom{left:840px;top:490px;width:145px;height:95px;transform:rotate(6deg);
  background:linear-gradient(135deg,var(--photo-dark),#6b5040)}
</style>
</head>
<body>
<section class="billboard">
  <div class="sheet"></div>
  <div class="hand hand--left" role="img" aria-label="Illustrated thumbs-up hand pointing right"></div>
  <div class="hand hand--right" role="img" aria-label="Illustrated thumbs-up hand"></div>

  <svg class="arrow" viewBox="0 0 440 80" aria-hidden="true">
    <polygon points="0,14 350,14 350,0 440,40 350,80 350,66 0,66" fill="var(--red)"/>
  </svg>
  <div class="tilt arrow-text">2 miles ahead on right</div>

  <div class="tilt brand">
    <div class="brand-name">Torvelli's</div>
    <div class="brand-sub">SOUTHWEST BAR &amp; GRILL</div>
  </div>

  <div class="tilt tagline">Good Food, Good Life</div>
  <div class="tilt headline headline--first">California</div>
  <div class="tilt headline headline--second">Cuisine</div>
  <div class="tilt venue">Historic Marbury Hill Inn</div>
  <div class="tilt phone">555.317.2968</div>
  <div class="tilt web">www.torvellis.com</div>

  <svg class="badge" viewBox="0 0 190 190" role="img" aria-label="Voted number 1 again">
    <circle cx="95" cy="95" r="92" fill="#c9c9c9"/>
    <circle cx="95" cy="95" r="80" fill="var(--red)"/>
    <text x="95" y="48" text-anchor="middle" font-family="Open Sans, sans-serif" font-weight="700" font-size="14" fill="#fff" letter-spacing="1">VOTED NUMBER</text>
    <text x="95" y="118" text-anchor="middle" font-family="Roboto Condensed, sans-serif" font-weight="700" font-size="70" fill="#fff">1</text>
    <text x="95" y="142" text-anchor="middle" font-family="Alfa Slab One, serif" font-size="20" fill="var(--gold)">again!</text>
    <text x="95" y="165" text-anchor="middle" font-size="16" fill="#fff">★ ★ ★</text>
  </svg>

  <div class="photo photo--top" role="img" aria-label="Photo of a couple sharing a meal"></div>
  <div class="photo photo--bottom" role="img" aria-label="Photo of a couple dining by candlelight"></div>
</section>
</body>
</html>
```